New letter head for Air Conditioning business

We need a new professional letter head design to suit our new re-branded air conditioning business. Our new logo is attached

```html
<!DOCTYPE html>
<html lang="en">
<head>
<meta charset="utf-8">
<title>Norvane Letterhead</title>
<link href="https://fonts.googleapis.com/css2?family=Montserrat:wght@400;600;700;800&display=swap" rel="stylesheet">
<style>
  :root {
    --ink: #3a3a3c;
    --green: #4cb96b;
    --red: #e8463f;
    --dark: #3b3b3d;
    --paper: #ffffff;
    --faint: #f1f1f1;
    --text: #4a4a4a;
  }
  html, body {
    margin: 0;
    padding: 0;
    overflow: hidden;
    background: var(--paper);
  }
  .letterhead {
    position: relative;
    width: 849px;
    height: 1200px;
    overflow: hidden;
    background: var(--paper);
    font-family: "Montserrat", sans-serif;
    color: var(--text);
  }
  .brand {
    position: absolute;
    left: 52px;
    top: 52px;
    display: flex;
    align-items: center;
    gap: 22px;
  }
  .brand-dot {
    width: 110px;
    height: 110px;
    border-radius: 50%;
    background: var(--green);
  }
  .brand-name {
    font-size: 58px;
    font-weight: 800;
    letter-spacing: 4px;
    color: var(--ink);
    line-height: 1;
  }
  .brand-tagline {
    margin-top: 10px;
    font-size: 13px;
    font-weight: 600;
    letter-spacing: 2.6px;
    color: var(--green);
  }
  .watermark {
    position: absolute;
    left: 0;
    right: 0;
    top: 560px;
    text-align: center;
    font-size: 120px;
    font-weight: 800;
    letter-spacing: 8px;
    color: var(--faint);
  }
  .contact {
    position: absolute;
    left: 58px;
    top: 1036px;
    font-size: 11.5px;
    font-weight: 600;
    color: var(--text);
  }
  .contact-row {
    display: flex;
    align-items: center;
    gap: 12px;
    margin-bottom: 9px;
  }
  .contact-icon {
    width: 20px;
    height: 20px;
    border-radius: 50%;
    background: var(--green);
    display: flex;
    align-items: center;
    justify-content: center;
    flex: none;
  }
  .contact-lines { line-height: 1.35; }
  .footer {
    position: absolute;
    left: 0;
    bottom: 0;
    width: 849px;
    height: 54px;
  }
  .footer svg { position: absolute; inset: 0; }
  .social {
    position: absolute;
    left: 26px;
    top: 18px;
    display: flex;
    align-items: center;
    gap: 6px;
    font-size: 11px;
    font-weight: 600;
    color: #fff;
  }
  .social-dot {
    width: 15px;
    height: 15px;
    border-radius: 50%;
    background: rgba(255,255,255,0.85);
  }
  .social-handle { margin-left: 6px; }
</style>
</head>
<body>
<div class="letterhead">
  <header class="brand">
    <div class="brand-dot"></div>
    <div>
      <div class="brand-name">NORVANE</div>
      <div class="brand-tagline">AIR CONDITIONING &amp; REFRIGERATION</div>
    </div>
  </header>

  <div class="watermark" aria-hidden="true">NORVANE</div>

  <section class="contact">
    <div class="contact-row">
      <span class="contact-icon">
        <svg width="10" height="12" viewBox="0 0 10 12"><path d="M5 0a4 4 0 0 1 4 4c0 3-4 8-4 8S1 7 1 4a4 4 0 0 1 4-4z" fill="#fff"/><circle cx="5" cy="4" r="1.5" fill="var(--green)"/></svg>
      </span>
      <span class="contact-lines">Post Box: 00000, Dubai, UAE</span>
    </div>
    <div class="contact-row">
      <span class="contact-icon">
        <svg width="10" height="10" viewBox="0 0 10 10"><path d="M2 0l2 2.5-1 1.2c.6 1.3 1.7 2.4 3 3l1.2-1L10 8 8.5 10C4 9.5.5 6 0 1.5z" fill="#fff"/></svg>
      </span>
      <span class="contact-lines">+0000 0000000<br>+0000 0000000</span>
    </div>
    <div class="contact-row">
      <span class="contact-icon">
        <svg width="11" height="8" viewBox="0 0 11 8"><rect x="0" y="0" width="11" height="8" rx="1" fill="#fff"/><path d="M0.5 0.8l5 3.6 5-3.6" stroke="var(--green)" stroke-width="1" fill="none"/></svg>
      </span>
      <span class="contact-lines">info@norvane-cooling</span>
    </div>
  </section>

  <footer class="footer">
    <svg width="849" height="54" viewBox="0 0 849 54">
      <polygon points="340,14 849,14 849,54 300,54" fill="var(--dark)"/>
      <polygon points="0,0 360,0 400,54 0,54" fill="var(--red)"/>
    </svg>
    <div class="social">
      <span class="social-dot"></span>
      <span class="social-dot"></span>
      <span class="social-dot"></span>
      <span class="social-dot"></span>
      <span class="social-dot"></span>
      <span class="social-handle">@norvane cooling</span>
    </div>
  </footer>
</div>
</body>
</html>
```